Design NEW business card

We would like a business card using the colour deep red wine or dark navy blue textured background (patterned or not, open to suggestions) with a high gloss debossed rose gold/copper RM Roland Mercer Jewellery business name (Provided). I have included images for your review we would like to keep our currently logo and business name on the front but you can change the layout and positioning. For the back of the card we are open to all suggestions/variations.
Business
Use our current RM Roland Mercer Jewellery logo (Provided image)

```html
<!DOCTYPE html>
<html lang="en">
<head>
<meta charset="utf-8">
<title>Roland Mercer Jewellery – Business Card</title>
<link rel="stylesheet" href="https://fonts.googleapis.com/css2?family=Montserrat:wght@300;400;500&display=swap">
<style>
  :root {
    --stage: #2a2523;
    --card: #3b2b34;
    --card-pattern-a: #3f2e38;
    --card-pattern-b: #36262f;
    --edge: #8a2a36;
    --copper: #c8906c;
    --ink: #ece6e9;
    --ink-soft: #cfc6cb;
  }
  * { margin: 0; padding: 0; box-sizing: border-box; }
  html, body {
    width: 1200px;
    height: 864px;
    overflow: hidden;
    background: var(--stage);
    font-family: "Montserrat", sans-serif;
  }
  .stage {
    position: relative;
    width: 1200px;
    height: 864px;
  }
  .card {
    position: absolute;
    width: 560px;
    height: 320px;
    background: var(--card);
    border-bottom: 3px solid var(--edge);
    overflow: hidden;
  }
  .card--front { left: 30px; top: 160px; }
  .card--back  { left: 610px; top: 384px; }
  .card__pattern {
    position: absolute;
    inset: 0;
    background: linear-gradient(135deg, var(--card-pattern-a), var(--card-pattern-b));
  }
  .brand {
    position: absolute;
    left: 70px;
    top: 130px;
    display: flex;
    align-items: center;
    gap: 16px;
  }
  .brand__dot {
    width: 40px;
    height: 40px;
    border-radius: 50%;
    background: var(--copper);
  }
  .brand__name {
    color: var(--copper);
    font-weight: 400;
    font-size: 22px;
    letter-spacing: 4px;
    text-transform: uppercase;
  }
  .contact {
    position: absolute;
    left: 40px;
    top: 118px;
    color: var(--ink-soft);
    font-weight: 400;
    font-size: 15px;
    line-height: 1.35;
  }
  .contact__name {
    color: var(--ink);
    font-weight: 500;
    font-size: 20px;
    letter-spacing: 0.5px;
    text-transform: uppercase;
  }
  .contact__role {
    text-transform: uppercase;
    font-size: 15px;
    margin-bottom: 2px;
  }
  .contact__label { font-weight: 500; color: var(--ink); }
  .contact__web { color: var(--ink); font-weight: 500; font-size: 17px; margin-top: 4px; }
</style>
</head>
<body>
<main class="stage">
  <section class="card card--front">
    <div class="card__pattern" role="img" aria-label="Repeating script monogram pattern in tonal plum"></div>
    <div class="brand">
      <span class="brand__dot"></span>
      <span class="brand__name">Roland Mercer Jewellery</span>
    </div>
  </section>

  <section class="card card--back">
    <div class="card__pattern" role="img" aria-label="Repeating script monogram pattern in tonal plum"></div>
    <div class="contact">
      <p class="contact__name">Evelyn Hart</p>
      <p class="contact__role">CEO/Founder</p>
      <p>214 Larchmont Row</p>
      <p>Fairhaven, Oregon 97120</p>
      <p><span class="contact__label">P.</span> 503 218 7746</p>
      <p><span class="contact__label">E.</span> evelyn@rolandmercer.com</p>
      <p class="contact__web">www.rolandmercer.com</p>
    </div>
  </section>
</main>
</body>
</html>
```